Business Card Design

New business card design

Target Market(s)

Residential & Commercial Property Managers

Industry/Entity Type

Plumbing Services

Contact Information for Business Card

Name - Rowan Keddle, title - Director, Phone Number - 0431 286 517, email - rowan@tbk-plumbing.com.au, Company ABN - 73 215 904 386,

Font styles to use
Sans Serif

Colors
0054AA
0677BA
7BADD7
CADEEF
E8F1F8

```html
<!DOCTYPE html>
<html lang="en">
<head>
<meta charset="utf-8">
<title>TBK Plumbing Services – Business Card</title>
<link rel="stylesheet" href="https://fonts.googleapis.com/css2?family=Poppins:wght@300;400;500;700&display=swap">
<style>
  :root {
    --stage: #222222;
    --paper: #ffffff;
    --ink: #1b232c;
    --taupe: #6e665c;
    --blue: #29abe2;
    --blue-soft: #6cc4ec;
    --white: #ffffff;
  }
  * { box-sizing: border-box; margin: 0; padding: 0; }
  html, body {
    width: 1200px; height: 711px; overflow: hidden;
    background: var(--stage);
    font-family: "Poppins", sans-serif;
  }
  .stage {
    position: relative; width: 1200px; height: 711px;
    display: flex; align-items: center; justify-content: center; gap: 40px;
  }
  .card {
    position: relative; width: 550px; height: 314px;
    background: var(--paper); overflow: hidden;
    box-shadow: 0 12px 30px rgba(0,0,0,.55);
  }

  /* wordmark */
  .wordmark {
    position: absolute; left: 0; right: 0;
    display: flex; flex-direction: column; align-items: center;
  }
  .wordmark__row { display: flex; align-items: center; gap: 14px; }
  .wordmark__name {
    font-weight: 500; color: var(--ink); line-height: 1; letter-spacing: 2px;
  }
  .wordmark__dot { border-radius: 50%; background: var(--blue); }
  .wordmark__tag {
    font-weight: 300; color: var(--taupe); text-transform: lowercase;
  }
  .card--front .wordmark { top: 78px; }
  .card--front .wordmark__name { font-size: 104px; }
  .card--front .wordmark__dot { width: 26px; height: 26px; margin-top: 40px; }
  .card--front .wordmark__tag { font-size: 15px; letter-spacing: 13px; margin-top: 14px; }

  .card--back .wordmark { top: 28px; }
  .card--back .wordmark__name { font-size: 66px; }
  .card--back .wordmark__dot { width: 17px; height: 17px; margin-top: 26px; }
  .card--back .wordmark__tag { font-size: 10px; letter-spacing: 9px; margin-top: 8px; }

  /* bands */
  .band-name {
    position: absolute; left: 0; top: 196px; width: 330px; height: 62px;
    background: var(--ink);
  }
  .band-contact {
    position: absolute; left: 318px; top: 142px; right: 0; height: 72px;
    background: var(--taupe);
  }
  .accent-circle {
    position: absolute; left: 290px; top: 158px; width: 74px; height: 74px;
    border-radius: 50%; background: var(--blue); border: 3px solid var(--white);
  }
  .person {
    position: absolute; left: 24px; top: 200px; width: 262px; text-align: right;
  }
  .person__name { font-size: 27px; line-height: 1.15; color: var(--blue-soft); font-weight: 400; }
  .person__first { color: var(--blue); font-weight: 700; }
  .person__title { font-size: 13px; color: var(--white); font-weight: 400; }

  .contact {
    position: absolute; left: 372px; top: 150px; width: 170px; list-style: none;
    color: var(--white); font-size: 10px; font-weight: 300; line-height: 19px;
  }
  .contact__item { display: flex; align-items: center; gap: 6px; white-space: nowrap; }
  .contact__icon { width: 12px; height: 12px; flex: none; }

  .abn {
    position: absolute; left: 318px; right: 0; top: 232px; text-align: center;
    color: var(--blue); font-size: 12px; font-weight: 300; letter-spacing: .5px;
  }
</style>
</head>
<body>
<main class="stage">

  <section class="card card--front" aria-label="Card front">
    <div class="wordmark">
      <div class="wordmark__row">
        <span class="wordmark__name">tbk</span>
        <span class="wordmark__dot"></span>
      </div>
      <span class="wordmark__tag">plumbing services</span>
    </div>
  </section>

  <section class="card card--back" aria-label="Card back">
    <div class="wordmark">
      <div class="wordmark__row">
        <span class="wordmark__name">tbk</span>
        <span class="wordmark__dot"></span>
      </div>
      <span class="wordmark__tag">plumbing services</span>
    </div>

    <div class="band-contact"></div>
    <div class="band-name"></div>
    <div class="accent-circle"></div>

    <div class="person">
      <p class="person__name"><span class="person__first">Rowan</span> Keddle</p>
      <p class="person__title">Director</p>
    </div>

    <ul class="contact">
      <li class="contact__item">
        <svg class="contact__icon" viewBox="0 0 16 16"><circle cx="8" cy="8" r="8" fill="#29abe2"/><path d="M5 4.5c.6-.4 1.2 0 1.5.7l.4 1c.1.4-.1.7-.4.9l-.4.3c.4.9 1.1 1.6 2 2l.3-.4c.2-.3.5-.5.9-.4l1 .4c.7.3 1.1.9.7 1.5-.7 1-2 1.2-3.3.4A8 8 0 0 1 4.6 7.8C3.8 6.5 4 5.2 5 4.5z" fill="#fff"/></svg>
        0431 286 517
      </li>
      <li class="contact__item">
        <svg class="contact__icon" viewBox="0 0 16 16"><circle cx="8" cy="8" r="8" fill="#29abe2"/><circle cx="8" cy="8" r="4.5" fill="none" stroke="#fff" stroke-width="1"/><path d="M3.5 8h9M8 3.5c-2 2.5-2 6.5 0 9M8 3.5c2 2.5 2 6.5 0 9" fill="none" stroke="#fff" stroke-width="1"/></svg>
        www.tbk-plumbing.com.au
      </li>
      <li class="contact__item">
        <svg class="contact__icon" viewBox="0 0 16 16"><circle cx="8" cy="8" r="8" fill="#29abe2"/><rect x="4" y="5" width="8" height="6" fill="none" stroke="#fff" stroke-width="1"/><path d="M4 5l4 3.5L12 5" fill="none" stroke="#fff" stroke-width="1"/></svg>
        rowan@tbk-plumbing.com.au
      </li>
    </ul>

    <p class="abn">ABN - 73 215 904 386</p>
  </section>

</main>
</body>
</html>
```